Book Cover for Productivity Book

I need a book cover for my latest publication "On Momentum: The Gathered Insights of the Swiftest Worker Breathing"

You can see my branding at www.quillmarrow.com

This is meant to be my epic pinaccle work on productivity, I want it to look like the end all be all word on productivity.

Target Market(s)

entrepreneurs

```html
<!DOCTYPE html>
<html lang="en">
<head>
<meta charset="utf-8">
<title>On Momentum – Book Cover</title>
<link rel="stylesheet" href="https://fonts.googleapis.com/css2?family=Oswald:wght@700&family=Montserrat:wght@700&display=swap">
<style>
  :root {
    --backdrop: #aad1d8;
    --cover-grey: #a4a4a4;
    --cover-red: #6a0000;
    --title-red: #6e0000;
    --subtitle-white: #ededed;
    --art-gold: #c9962a;
    --art-chalk: #a8605a;
    --art-edge: #7e1c16;
  }
  html, body {
    margin: 0;
    padding: 0;
    width: 1200px;
    height: 1200px;
    overflow: hidden;
    background: var(--backdrop);
  }
  .canvas {
    position: relative;
    width: 1200px;
    height: 1200px;
  }
  .book-cover {
    position: absolute;
    left: 238px;
    top: 60px;
    width: 724px;
    height: 1080px;
    display: block;
  }
  .cover-top { fill: var(--cover-grey); }
  .cover-bottom { fill: var(--cover-red); }
  .title {
    font-family: "Oswald", "Arial Narrow", sans-serif;
    font-weight: 700;
    font-size: 116px;
    fill: var(--title-red);
    text-transform: uppercase;
  }
  .subtitle {
    font-family: "Montserrat", Arial, sans-serif;
    font-weight: 700;
    font-size: 37px;
    fill: var(--subtitle-white);
  }
</style>
</head>
<body>
<div class="canvas">
  <svg class="book-cover" viewBox="0 0 724 1080" xmlns="http://www.w3.org/2000/svg" aria-label="Book cover: On Momentum">
    <defs>
      <radialGradient id="ideas-fill" cx="50%" cy="95%" r="75%" fx="50%" fy="95%">
        <stop offset="0%" stop-color="var(--art-gold)"/>
        <stop offset="30%" stop-color="#b77a3e"/>
        <stop offset="65%" stop-color="var(--art-chalk)"/>
        <stop offset="100%" stop-color="var(--art-edge)"/>
      </radialGradient>
    </defs>

    <rect class="cover-top" x="0" y="0" width="724" height="1080"/>
    <polygon class="cover-bottom" points="0,594 724,259 724,1080 0,1080"/>

    <rect class="cover-illustration" x="50" y="660" width="600" height="420" rx="28" fill="url(#ideas-fill)"
          role="img" aria-label="Chalk illustration of a gold head with ideas flowing out: clock, heart, light bulb, eye, money and notes"/>

    <g class="title-block" transform="translate(150 514) rotate(-24.8)">
      <text class="title title-small" x="-48" y="-100">On</text>
      <text class="title title-main" x="0" y="0">Momentum</text>
      <text class="subtitle subtitle-line" x="-96" y="75">The Gathered Insights of the</text>
      <text class="subtitle subtitle-line" x="-50" y="132">Swiftest Worker Breathing</text>
    </g>
  </svg>
</div>
</body>
</html>
```